Company Profile

Redesign of Business Profile for print in A4 format. The design pages should complete a booklet. Kindly use Pictures as well as projects from our website @zwilobeniproperties.co.za

Business, Construction

```html
<!DOCTYPE html>
<html lang="en">
<head>
<meta charset="utf-8">
<title>Zwilobeni Properties – About Us</title>
<link rel="stylesheet" href="https://fonts.googleapis.com/css2?family=Nunito:wght@300;700&family=Roboto+Condensed:wght@300;400&display=swap">
<style>
  :root {
    --charcoal: #353233;
    --maroon: #862b1f;
    --white: #ffffff;
    --ink: #111111;
    --tagline: #a9a9a9;
    --body-text: #e4e4e4;
    --sky-top: #8fb3d6;
    --sky-low: #c9d6df;
    --ground: #cdb9a2;
  }
  html, body {
    margin: 0;
    padding: 0;
    overflow: hidden;
    background: #ffffff;
  }
  .page {
    position: relative;
    width: 848px;
    height: 1200px;
    overflow: hidden;
    background: var(--charcoal);
    font-family: "Roboto Condensed", sans-serif;
    color: var(--body-text);
  }
  .decor {
    position: absolute;
    inset: 0;
    width: 848px;
    height: 1200px;
  }
  .web-address {
    position: absolute;
    left: 38px;
    top: 20px;
    font-family: "Nunito", sans-serif;
    font-weight: 300;
    font-size: 15px;
    letter-spacing: 0.3px;
    color: #d8d8d8;
  }
  .tagline {
    font-family: "Nunito", sans-serif;
    font-weight: 300;
    font-size: 31px;
    fill: var(--tagline);
    letter-spacing: 1px;
  }
  .content {
    position: absolute;
    right: 56px;
    top: 0;
    width: 460px;
    text-align: right;
  }
  .section-title {
    position: absolute;
    right: 0;
    margin: 0;
    font-family: "Nunito", sans-serif;
    font-weight: 700;
    font-size: 23px;
    letter-spacing: 0.3px;
    color: var(--white);
    white-space: nowrap;
  }
  .section-text {
    position: absolute;
    right: 0;
    margin: 0;
    font-weight: 300;
    white-space: nowrap;
  }
  .about-text {
    font-size: 13.2px;
    line-height: 15.7px;
    text-transform: uppercase;
  }
  .statement {
    font-size: 17px;
  }
  .values-text {
    font-size: 17px;
    line-height: 15.7px;
  }
  .values-list {
    position: absolute;
    right: 0;
    margin: 0;
    padding: 0;
    list-style: none;
    font-weight: 300;
    font-size: 17.5px;
    line-height: 15.7px;
  }
  .brand {
    position: absolute;
    left: 24px;
    top: 1140px;
    display: flex;
    align-items: center;
    gap: 10px;
    color: var(--white);
    font-family: "Nunito", sans-serif;
    font-weight: 700;
    font-size: 23px;
    white-space: nowrap;
  }
  .brand-mark {
    width: 16px;
    height: 16px;
    background: var(--white);
  }
</style>
</head>
<body>
<main class="page">

  <svg class="decor" viewBox="0 0 848 1200" xmlns="http://www.w3.org/2000/svg">
    <defs>
      <linearGradient id="photoTones" x1="0" y1="0" x2="0" y2="1">
        <stop offset="0" stop-color="var(--sky-top)"/>
        <stop offset="0.35" stop-color="var(--sky-low)"/>
        <stop offset="0.7" stop-color="#b9b6b2"/>
        <stop offset="1" stop-color="var(--ground)"/>
      </linearGradient>
      <filter id="softShadow" x="-20%" y="-20%" width="140%" height="140%">
        <feDropShadow dx="6" dy="4" stdDeviation="7" flood-color="#000" flood-opacity="0.55"/>
      </filter>
      <path id="taglineCurve" d="M 445 16 C 530 72 630 122 740 152"/>
    </defs>

    <path class="swoosh-red" fill="var(--maroon)" d="M 210 0 C 330 92 520 176 728 215 C 600 152 450 72 362 0 Z"/>
    <path class="swoosh-red" fill="var(--maroon)" d="M 480 0 H 848 V 150 C 720 120 590 62 480 0 Z"/>
    <path class="swoosh-white" fill="var(--white)" filter="url(#softShadow)" d="M 340 0 C 460 84 650 170 848 216 V 156 C 710 130 575 70 482 0 Z"/>
    <text class="tagline"><textPath href="#taglineCurve">achieving distinction</textPath></text>

    <ellipse class="photo-frame" cx="0" cy="473" rx="386" ry="387" fill="url(#photoTones)" filter="url(#softShadow)" role="img" aria-label="Photograph of a completed multi-storey building on a construction site with a worker in front"/>

    <path class="swoosh-red" fill="var(--maroon)" d="M 0 865 C 250 1080 600 1182 848 1162 V 1200 H 0 Z"/>
    <path fill="none" stroke="var(--white)" stroke-width="8" d="M 0 872 C 230 1070 560 1172 848 1178"/>
    <path fill="none" stroke="var(--ink)" stroke-width="5" d="M 40 905 C 270 1070 560 1150 848 1160"/>
    <path class="swoosh-red" fill="var(--maroon)" d="M 60 918 C 300 1060 560 1120 848 1132 L 848 1156 C 560 1142 300 1082 60 918 Z"/>
    <rect class="corner-tab" x="759" y="1145" width="120" height="44" rx="22" fill="var(--white)"/>
  </svg>

  <div class="web-address">www.zwilobeni.co.za</div>

  <section class="content">
    <h2 class="section-title" style="top:268px">ABOUT US</h2>
    <p class="section-text about-text" style="top:309px">
      Our culture of teamwork, founded on the need for<br>
      collaboration and partnership, guides our<br>
      interaction with clients, and is the basis of our<br>
      approach to every construction project we have<br>
      successfully completed from our inception.
    </p>

    <h2 class="section-title" style="top:449px">OUR VISION</h2>
    <p class="section-text statement" style="top:483px">An Infrastructure provider of distinction.</p>

    <h2 class="section-title" style="top:575px">OUR MISSION</h2>
    <p class="section-text statement" style="top:607px">Restore people’s dignity through infrastructure development.</p>

    <h2 class="section-title" style="top:697px">OUR VALUES</h2>
    <p class="section-text values-text" style="top:740px">
      In pursuit of our vision and mission, our values outline<br>
      the PATH to our growth into a housing and<br>
      infrastructure development company that places our<br>
      clients at the forefront of all our interventions through:
    </p>
    <ul class="values-list" style="top:820px">
      <li>PROFESSIONALISM</li>
      <li>ACCOUNTABILITY</li>
      <li>TRANSPARENCY</li>
      <li>HONESTY</li>
    </ul>
  </section>

  <div class="brand">
    <span class="brand-mark"></span>
    <span class="brand-name">Zwilobeni Properties</span>
  </div>

</main>
</body>
</html>
```